Classy, Elegant, Simple Business Card Design

Looking to have a classy, simple, and elegant design. Want a top notch designed business card. I really like the look of the new torvane credit card. I also like the design I attached. I am trying to reach 21-29 year old females for booking us for there wedding or event. We offer Disc Jockey Service, Photo Booth Rentals, and Uplighting .

Target Market(s)

21-28 year old females

Contact Information for Business Card

Has to have logo, website, email, and phone number

Font styles to use
Other font styles liked:
• open to font choice, modern, clean
Designer to choose
33a6d7
0791cd
0555a3
ffffff

Requirements
Must have
• Has to have logo, website, email, and phone number
Nice to have
• I really like the design of the new torvane credit card. I also included my logo and some designs I like
Should not have
• clutter or too much info

```html
<!DOCTYPE html>
<html lang="en">
<head>
<meta charset="utf-8">
<title>Brightline Event Group – Business Card</title>
<link rel="stylesheet" href="https://fonts.googleapis.com/css2?family=Lato:wght@400;700&display=swap">
<style>
  :root {
    --backdrop: #e8e5e1;
    --card-white: #ffffff;
    --navy: #12325e;
    --sky: #1a8fd6;
    --bright: #0791cd;
    --muted: #8a8f96;
    --text-light: #ffffff;
  }
  * { margin: 0; padding: 0; box-sizing: border-box; }
  html, body {
    width: 1200px;
    height: 900px;
    overflow: hidden;
    background: var(--backdrop);
    font-family: "Lato", Arial, sans-serif;
  }
  .canvas {
    position: relative;
    width: 1200px;
    height: 900px;
  }
  .business-card {
    position: absolute;
    left: 322px;
    top: 278px;
    width: 556px;
    height: 344px;
    background: var(--card-white);
    overflow: hidden;
    box-shadow: 2px 3px 6px rgba(0, 0, 0, 0.35);
  }
  .wave-area {
    position: absolute;
    left: 0;
    right: 0;
    top: 196px;
    bottom: 0;
    background: linear-gradient(180deg, var(--sky) 0%, var(--navy) 22%, var(--navy) 100%);
  }
  .brand {
    position: absolute;
    left: 26px;
    top: 40px;
    width: 200px;
    text-align: center;
  }
  .brand-mark {
    display: block;
    width: 72px;
    height: 72px;
    margin: 0 auto 18px;
    border-radius: 50%;
    background: var(--bright);
  }
  .brand-name {
    display: block;
    color: var(--navy);
    font-weight: 700;
    font-size: 30px;
    letter-spacing: 1px;
    line-height: 1;
  }
  .brand-sub {
    display: block;
    margin-top: 3px;
    color: var(--muted);
    font-size: 11px;
    letter-spacing: 5.5px;
    line-height: 1;
  }
  .contact-list {
    position: absolute;
    right: 24px;
    top: 218px;
    list-style: none;
    color: var(--text-light);
    font-size: 15px;
    line-height: 20.5px;
    text-align: right;
  }
  .contact-list li {
    display: flex;
    justify-content: flex-end;
    align-items: center;
    gap: 4px;
  }
  .contact-icon {
    width: 13px;
    height: 13px;
    flex: none;
  }
  .services {
    position: absolute;
    right: 26px;
    top: 293px;
    color: var(--text-light);
    font-size: 16.5px;
    white-space: nowrap;
  }
</style>
</head>
<body>
  <main class="canvas">
    <article class="business-card">
      <div class="wave-area" role="img" aria-label="Flowing wave decoration in sky blue and navy"></div>

      <div class="brand">
        <span class="brand-mark"></span>
        <span class="brand-name">BRIGHTLINE</span>
        <span class="brand-sub">EVENT GROUP</span>
      </div>

      <ul class="contact-list">
        <li>044-555 0187
          <svg class="contact-icon" viewBox="0 0 16 16" aria-label="phone"><path d="M2,6 C2,3 14,3 14,6 L11,7 L10,5.5 L6,5.5 L5,7 Z M4,8 L12,8 L13,13 L3,13 Z" fill="#fff"/></svg>
        </li>
        <li>info@brightline.com
          <svg class="contact-icon" viewBox="0 0 16 16" aria-label="email"><rect x="1" y="3" width="14" height="10" fill="#fff"/><path d="M1.5,3.5 L8,9 L14.5,3.5" fill="none" stroke="var(--navy)" stroke-width="1.3"/></svg>
        </li>
        <li>www.brightline-events.com
          <svg class="contact-icon" viewBox="0 0 16 16" aria-label="website"><circle cx="8" cy="8" r="7" fill="#fff"/><path d="M5,4 C7,5 6,7 8,8 C9,9 7,11 8,13 M10,3 C11,5 13,5 13,7" fill="none" stroke="var(--navy)" stroke-width="1.3"/></svg>
        </li>
      </ul>

      <p class="services">Disc Jockey Service | Uplighting | Photo Booth Rentals</p>
    </article>
  </main>
</body>
</html>
```